Business card design Needed for new logo / Construction business, home extensions and new builds

We need a business card design using our new logo files which i will attach to this project :)

We are a small construction business specialising in home extensions, new builds and property development. We are very ambitious and would appreciate professional and elegant designs for our new business card.

Very serious about using the services on MakerQuarry and recently acquired our new logo from here :)

Please get involved, i will feedback when i can as i am very busy but can respond daily, thanks

Target Market(s)

People that want to build onto their houses, new building developments or adding too their existing property

Industry/Entity Type

Construction

Contact Information for Business Card

Renwick Tolliver Construction, Lionel Ashby (Managing Director), Tel 07822254961, email - info@renwick-tolliver, www.renwick-tolliver.co.uk

Colors

Designer to choose colors to be used in the design.

Requirements
Must have
• I like a deep grey on the back please. A lot of you have provided black from and back, try mixing things up a little. The black looks cool 😎 Thanks

```html
<!DOCTYPE html>
<html lang="en">
<head>
<meta charset="utf-8">
<title>Renwick Tolliver Construction – Business Card</title>
<link href="https://fonts.googleapis.com/css2?family=EB+Garamond:wght@400;600&display=swap" rel="stylesheet">
<style>
  :root {
    --backdrop: #5b5b5b;
    --card-black: #060606;
    --card-deep: #141414;
    --card-grey: #2a2a2a;
    --gold: #c9952f;
    --gold-dark: #5a4320;
    --silver: #d6d6d6;
    --text-light: #e8e8e8;
    --text-dim: #bdbdbd;
  }
  * { box-sizing: border-box; margin: 0; padding: 0; }
  html, body { width: 1200px; height: 900px; overflow: hidden; }
  body {
    background: var(--backdrop);
    font-family: "EB Garamond", Georgia, serif;
    position: relative;
  }
  .card {
    position: absolute;
    width: 640px;
    height: 366px;
    border-radius: 22px;
    overflow: hidden;
    box-shadow: 0 14px 30px rgba(0,0,0,0.45);
  }
  /* Back side */
  .card-back {
    left: 120px; top: 70px;
    background: var(--card-deep);
  }
  .back-pattern {
    position: absolute; inset: 0;
    background: radial-gradient(ellipse at 50% 50%, var(--card-grey) 0%, var(--card-deep) 55%, var(--card-black) 100%);
  }
  .back-mark {
    position: absolute;
    right: 70px; top: 150px;
    display: flex; align-items: center; gap: 8px;
    color: var(--gold);
    font-weight: 600;
    font-size: 15px;
    letter-spacing: 1px;
  }
  .mark-square {
    width: 12px; height: 12px;
    background: var(--gold);
  }
  /* Front side */
  .card-front {
    left: 440px; top: 464px;
    background: var(--card-black);
  }
  .front-decoration {
    position: absolute;
    left: 0; bottom: 0;
    width: 330px; height: 220px;
    background: linear-gradient(160deg, #1c1c1c 0%, #15120c 45%, var(--gold-dark) 100%);
    opacity: 0.75;
  }
  .person {
    position: absolute;
    left: 42px; top: 58px;
  }
  .person-name {
    color: var(--gold);
    font-weight: 600;
    font-size: 21px;
    letter-spacing: 0.5px;
  }
  .person-role {
    color: var(--text-dim);
    font-size: 16px;
    margin-top: 2px;
  }
  .contact-list {
    position: absolute;
    left: 372px; top: 48px;
    list-style: none;
  }
  .contact-item {
    display: flex; align-items: center; gap: 10px;
    color: var(--text-light);
    font-size: 16px;
    height: 27px;
  }
  .contact-icon { width: 14px; height: 14px; flex: none; }
  .divider {
    position: absolute;
    left: 360px; top: 150px;
    width: 250px; height: 1px;
    background: linear-gradient(90deg, transparent, var(--gold) 25%, var(--gold) 75%, transparent);
  }
  .company {
    position: absolute;
    right: 40px; top: 196px;
    display: flex; align-items: center; gap: 12px;
  }
  .company-square {
    width: 22px; height: 22px;
    background: var(--gold);
  }
  .company-name {
    color: var(--silver);
    font-size: 22px;
    font-weight: 400;
    letter-spacing: 1px;
    line-height: 1.1;
    text-transform: uppercase;
  }
</style>
</head>
<body>

  <section class="card card-back" aria-label="Card back">
    <div class="back-pattern" role="img" aria-label="Tonal repeating monogram pattern on deep grey"></div>
    <div class="back-mark">
      <span class="mark-square"></span>
      <span>Renwick Tolliver</span>
    </div>
  </section>

  <section class="card card-front" aria-label="Card front">
    <div class="front-decoration" role="img" aria-label="Large faint brand mark decoration in dark grey and bronze"></div>

    <div class="person">
      <p class="person-name">LIONEL ASHBY</p>
      <p class="person-role">Managing Director</p>
    </div>

    <ul class="contact-list">
      <li class="contact-item">
        <svg class="contact-icon" viewBox="0 0 16 16" fill="#cfcfcf"><path d="M3 2h3l1 4-2 1a9 9 0 0 0 4 4l1-2 4 1v3c0 1-1 2-2 2A13 13 0 0 1 1 4c0-1 1-2 2-2z"/></svg>
        <span>07822254961</span>
      </li>
      <li class="contact-item">
        <svg class="contact-icon" viewBox="0 0 16 16" fill="none" stroke="#cfcfcf" stroke-width="1.5"><rect x="1" y="3" width="14" height="10"/><path d="M1 3l7 6 7-6"/></svg>
        <span>info@renwick-tolliver.co.uk</span>
      </li>
      <li class="contact-item">
        <svg class="contact-icon" viewBox="0 0 16 16" fill="none" stroke="#cfcfcf" stroke-width="1.3"><circle cx="8" cy="8" r="6.5"/><path d="M1.5 8h13M8 1.5c-3 3.5-3 9.5 0 13M8 1.5c3 3.5 3 9.5 0 13"/></svg>
        <span>www.renwick-tolliver.co.uk</span>
      </li>
    </ul>

    <div class="divider"></div>

    <div class="company">
      <span class="company-square"></span>
      <p class="company-name">Renwick Tolliver<br>Construction</p>
    </div>
  </section>

</body>
</html>
```